Brightway Haul & Upkeep Services, are a company that offers a 'one stop shop' pre-move clean up a

I have already selected a logo which I would like on the front of the business cards along with phone numbers, web address and email which are:
0487650392
www.brightwayhaul.com.au
brightwayhaulandupkeep@mailbox.example

On the back of the card I would like to list some of the types of service we offer (clean - move - repairs/maintenance) which are:
CLEAN - windows, gutters, solar panels, driveways/paths, carpets.
MOVE - Small/medium size house/office moves, large item pick-up & delivery, yard clean-up and removal.
General maintenance and repairs.

I would like the blue logo on a gray background.

Thanks

```html
<!DOCTYPE html>
<html lang="en">
<head>
<meta charset="utf-8">
<title>Brightway Haul &amp; Upkeep Services – Business Cards</title>
<link rel="stylesheet" href="https://fonts.googleapis.com/css2?family=Open+Sans:wght@400;600;700&display=swap">
<style>
  :root {
    --brand-blue: #1f69b4;
    --curl-dark: #2b2b2b;
    --curl-mid: #5a5a5a;
    --ink: #222222;
    --card: #ffffff;
    --backdrop: #d6d6d6;
  }
  * { margin: 0; padding: 0; box-sizing: border-box; }
  html, body {
    width: 1200px; height: 390px; overflow: hidden;
    background: var(--backdrop);
    font-family: "Open Sans", Arial, sans-serif;
  }
  .sheet { position: relative; width: 1200px; height: 390px; }
  .card {
    position: absolute; top: 45px; width: 558px; height: 312px;
    background: var(--card); overflow: hidden;
    box-shadow: 0 2px 6px rgba(0,0,0,.25);
  }
  .card--front { left: 42px; }
  .card--back { left: 625px; }

  .corner-flap { position: absolute; inset: 0; width: 558px; height: 312px; }

  .phone {
    position: absolute; top: 26px; right: 34px;
    color: #fff; font-size: 18px; letter-spacing: .5px;
    display: flex; align-items: center; gap: 6px;
  }
  .phone svg { width: 15px; height: 15px; }

  .brand-name {
    color: var(--brand-blue); font-weight: 700; line-height: 1.1;
    display: flex; align-items: center; gap: 12px;
  }
  .brand-name .brand-square { width: 22px; height: 22px; background: var(--brand-blue); flex: none; }
  .card--front .brand-name { position: absolute; left: 32px; top: 118px; font-size: 30px; }
  .card--back .brand-name {
    position: absolute; left: 0; right: 0; top: 82px;
    justify-content: center; font-size: 32px; text-align: center;
  }

  .contact-list {
    position: absolute; left: 30px; top: 240px; list-style: none;
    font-size: 15px; color: var(--ink);
  }
  .contact-list li { display: flex; align-items: center; gap: 7px; margin-bottom: 6px; }
  .contact-list svg { width: 12px; height: 12px; flex: none; }

  .services {
    position: absolute; left: 0; right: 0; top: 206px; text-align: center;
  }
  .services__title {
    color: var(--brand-blue); font-weight: 700; font-size: 21px; letter-spacing: 1.5px;
    margin-bottom: 12px;
  }
  .services__row {
    font-weight: 600; font-size: 16px; color: var(--ink); margin-bottom: 7px;
  }
  .services__row span + span { margin-left: 14px; }
  .bullet { color: var(--brand-blue); margin-right: 4px; }
</style>
</head>
<body>
<main class="sheet">
  <section class="card card--front" aria-label="Card front">
    <svg class="corner-flap" viewBox="0 0 558 312" aria-hidden="true">
      <defs>
        <linearGradient id="curlShade" x1="0" y1="0" x2="1" y2="1">
          <stop offset="0" stop-color="var(--curl-mid)"/>
          <stop offset=".6" stop-color="var(--curl-dark)"/>
          <stop offset="1" stop-color="#111"/>
        </linearGradient>
      </defs>
      <path d="M250 0 H558 V112 C535 112 518 125 510 150 Z" fill="var(--brand-blue)"/>
      <path d="M250 0 L510 150 C518 125 535 112 558 112 C532 132 512 165 500 198 Z" fill="url(#curlShade)"/>
    </svg>
    <div class="phone">
      <svg viewBox="0 0 16 16"><circle cx="8" cy="8" r="7" fill="none" stroke="#fff" stroke-width="1.3"/><path d="M5.5 4.5 l1.5 0 .5 2 -1 .8 c.5 1.2 1.2 2 2.4 2.5 l.8-1 2 .6 0 1.5 c-3.5.3-6.6-2.9-6.2-6.4z" fill="#fff"/></svg>
      <span>0487650392</span>
    </div>
    <h1 class="brand-name"><span class="brand-square"></span><span>Brightway Haul<br>&amp; Upkeep Services</span></h1>
    <ul class="contact-list">
      <li>
        <svg viewBox="0 0 12 12"><circle cx="6" cy="6" r="5.3" fill="none" stroke="var(--brand-blue)" stroke-width="1.2"/><ellipse cx="6" cy="6" rx="2.2" ry="5.3" fill="none" stroke="var(--brand-blue)" stroke-width="1"/><path d="M.7 6 H11.3" stroke="var(--brand-blue)"/></svg>
        <span>www.brightwayhaul.com.au</span>
      </li>
      <li>
        <svg viewBox="0 0 12 12"><rect x=".5" y="2.5" width="11" height="7.5" fill="var(--brand-blue)"/><path d="M.5 2.5 L6 7 L11.5 2.5" fill="none" stroke="#fff" stroke-width="1"/></svg>
        <span>brightwayhaulandupkeep@mailbox.example</span>
      </li>
    </ul>
  </section>

  <section class="card card--back" aria-label="Card back">
    <h2 class="brand-name"><span class="brand-square"></span><span>Brightway Haul<br>&amp; Upkeep Services</span></h2>
    <div class="services">
      <p class="services__title">Services we offer</p>
      <p class="services__row"><span><span class="bullet">•</span>Clean</span><span><span class="bullet">•</span>Move</span></p>
      <p class="services__row"><span class="bullet">•</span>General Maintenance And Repairs.</p>
    </div>
  </section>
</main>
</body>
</html>
```